Skiing Company Needs A5 28page Skiing Catalogue

ABOUT THE BUSINESS/COMPANY:
- We are a guided skiing company called "Silver Lantern Journeys" and "Kestrel Ridge Alpine Society".

ABOUT THE CATALOGUE:

- We need an A5 28 page catalogue. ALL THE FILES (like photos and logos) are in the zip folders.

- You can look at the 000 KRS Catalog Word Document. Instructions on what text and photos to use are labeled there per Page.

Target Market(s)

Advanced/ Expert Skiers and Snowboarders that are thinking of joining a tour

Industry/Entity Type

Travel Agent

Font styles to use
Serif

Colors
ffffff
ec1f27
0455a3

Requirements
Must have
• NEED a 3mm bleed
• This is included on the 000 KRS Catalog word document
Nice to have
• Our main color is dark blue (just like our logo). Some red is ok but the main focus should be the dark blue.
Should not have
• Words/ Letters in the color red

```html
<!DOCTYPE html>
<html lang="en">
<head>
<meta charset="utf-8">
<title>Silver Lantern Journeys — 2017-2018 Product Catalog Cover</title>
<link rel="stylesheet" href="https://fonts.googleapis.com/css2?family=Montserrat:wght@300;700&display=swap">
<style>
  :root {
    --page-bg: #ecebe8;
    --brand-blue: #0455a3;
    --band-dark: #2b2b2b;
    --title-light: #d9d9dc;
    --snow-light: #f4f7fb;
    --snow-shadow: #b9cbe0;
    --sky-blue: #dfe6ee;
    --mono-light: #ffffff;
    --mono-dark: #000000;
    --logo-ink: #2b2b2b;
  }
  html, body {
    margin: 0;
    padding: 0;
    width: 1200px;
    height: 1200px;
    overflow: hidden;
    background: var(--page-bg);
  }
  .canvas {
    position: relative;
    width: 1200px;
    height: 1200px;
  }
  .catalog-spread {
    position: absolute;
    left: 50px;
    top: 211px;
    width: 1100px;
    height: 778px;
    box-shadow: 0 6px 18px rgba(0,0,0,0.18);
  }
  .blue-panel { fill: var(--brand-blue); }
  .diagonal-band { fill: var(--band-dark); }
  .spine { stroke: rgba(0,0,0,0.06); stroke-width: 2; }
  .catalog-year {
    font-family: "Montserrat", sans-serif;
    font-weight: 700;
    font-size: 44px;
    fill: var(--title-light);
  }
  .catalog-title {
    font-family: "Montserrat", sans-serif;
    font-weight: 300;
    font-size: 29px;
    letter-spacing: 1px;
    fill: var(--title-light);
  }
  .partner-name {
    font-family: "Montserrat", sans-serif;
    font-weight: 700;
    font-size: 13px;
    letter-spacing: 0.5px;
    fill: var(--logo-ink);
  }
  .partner-dot { fill: var(--logo-ink); }
</style>
</head>
<body>
<div class="canvas">
  <svg class="catalog-spread" viewBox="0 0 1250 884" xmlns="http://www.w3.org/2000/svg">
    <defs>
      <linearGradient id="mountainPhotoTone" x1="0" y1="0" x2="1" y2="1">
        <stop offset="0" stop-color="#f6f8fb"/>
        <stop offset="0.45" stop-color="#e6edf5"/>
        <stop offset="0.75" stop-color="#c9d6e4"/>
        <stop offset="1" stop-color="#eef2f7"/>
      </linearGradient>
      <radialGradient id="skierPhotoTone" cx="0.15" cy="0.15" r="1">
        <stop offset="0" stop-color="#ffffff"/>
        <stop offset="0.45" stop-color="#bdbdbd"/>
        <stop offset="0.75" stop-color="#202020"/>
        <stop offset="1" stop-color="#000000"/>
      </radialGradient>
    </defs>

    <!-- back cover photo area -->
    <rect class="skier-photo" x="0" y="280" width="625" height="604" fill="url(#skierPhotoTone)"
          role="img" aria-label="Black and white photo of a skier carving through deep powder, silhouetted against bright spray"/>

    <!-- front cover title panel -->
    <rect class="blue-panel" x="625" y="500" width="625" height="384"/>

    <!-- mountain photo across the spread -->
    <polygon class="mountain-photo" points="0,0 1250,0 1250,682 980,582 980,697 0,290"
             fill="url(#mountainPhotoTone)"
             role="img" aria-label="Photo of a snowboarder riding a steep powder slope with snow-covered trees and a valley below"/>

    <line class="spine" x1="625" y1="0" x2="625" y2="884"/>

    <!-- stepped diagonal band -->
    <polygon class="diagonal-band" points="0,290 980,697 980,582 1250,682 1250,716 1010,624 1010,740 0,326"/>

    <!-- partner names -->
    <g class="partner-marks">
      <circle class="partner-dot" cx="1000" cy="110" r="6"/>
      <text class="partner-name" x="1012" y="106">KESTREL RIDGE</text>
      <text class="partner-name" x="1012" y="122">ALPINE SOCIETY</text>
      <text class="partner-name" x="1012" y="148">SILVER LANTERN</text>
      <text class="partner-name" x="1012" y="164">JOURNEYS</text>
    </g>

    <!-- cover title -->
    <text class="catalog-year" x="673" y="770">2017-2018</text>
    <text class="catalog-title" x="673" y="808">PRODUCT CATALOG</text>
  </svg>
</div>
</body>
</html>
```